Redesign Craft Brewing Recipe Website

Originally built with Bootstrap just to get the site going, I am seeking a complete redesign of the sites home page and recipe page. I am an experienced web developer with no graphic background, initially just looking for psd mocks.

I prefer styles that are clean and modern, and would prefer anything that is fun, engaging, and has an organic feel to it. I currently have a cartoon rabbit as a logo, but it needs some modification/tweaking, so any help in that area would be great as well.

Current site:
http://velvetfinch.cloudpagehost.net/

Current launch page/logo:
http://www.velvetfinch.com/

I like the overall layout of the elements currently, but the design sucks.

The launch page is at the following URL

Reason: Still looking for a more modern design. Designs received so far are too similar to the original.

My site is content based and does not contain images or products. Your design should not consist of large images.

Reason: The website has very little images, so the designs need to be more text and content based. The header needs to be very small and should not contain an ad rotater.

Target Market(s)

Home brewers, Craft brewers, Microbreweries, Brewpubs

Requirements
Must have
• Web 2.0 Look and Feel, Fun, Hip, Focus on content
Should not have
• A large photo as a header

```html
<!DOCTYPE html>
<html lang="en">
<head>
<meta charset="utf-8">
<title>Velvetfinch – Latest Recipes</title>
<link href="https://fonts.googleapis.com/css2?family=Signika:wght@400;600&family=PT+Sans:wght@400;700&family=PT+Sans+Narrow:wght@400;700&display=swap" rel="stylesheet">
<style>
:root{
  --maroon:#650000;
  --tan:#c5a574;
  --tan-dark:#b0905e;
  --lime:#b4c000;
  --nav-active:#c8d400;
  --wine:#a00c0c;
  --orange:#d98a12;
  --green-title:#3f5f00;
  --yellow:#ede000;
  --amber:#c98f0a;
  --ink:#333;
  --muted:#999;
  --page:#eeede9;
  --line:#dcdcdc;
  --bar:#3b3b3b;
}
*{box-sizing:border-box;margin:0;padding:0}
html,body{width:1162px;height:1200px;overflow:hidden}
body{background:var(--page);font-family:"PT Sans",sans-serif;color:var(--ink);position:relative}

/* header */
.site-header{height:114px;background:var(--maroon);position:relative}
.brand{position:absolute;left:126px;top:24px;display:flex;align-items:center;gap:14px}
.brand-dot{width:70px;height:70px;border-radius:50%;background:var(--tan)}
.brand-name{font-family:"Signika",sans-serif;font-weight:600;font-size:40px;line-height:1;color:var(--tan)}
.brand-tag{font-size:12.5px;line-height:14px;color:var(--tan-dark);margin-top:4px}
.main-nav{position:absolute;right:106px;top:0;height:114px;display:flex;gap:37px}
.main-nav a{font-family:"PT Sans",sans-serif;font-size:14.5px;color:#e6cfa8;text-decoration:none;line-height:122px;position:relative}
.main-nav a.active{color:var(--nav-active)}
.main-nav a.active::after{content:"";position:absolute;left:-10px;right:-10px;bottom:0;height:4px;background:var(--nav-active)}

/* sidebar */
.sidebar{position:absolute;left:106px;top:141px;width:231px;height:995px;background:#fff;border:1px solid var(--line);border-radius:3px;padding:0 12px}
.side-title{font-family:"Signika",sans-serif;font-weight:400;font-size:21px;line-height:24px;color:#444;margin:22px 0 9px 6px}
.side-title:first-child{margin-top:34px}
.side-title span{color:var(--tan)}
.field{height:30px;border:1px solid var(--line);font-size:14px;color:#555;padding:0 21px;display:flex;align-items:center;justify-content:space-between}
.field.placeholder{color:#aaa}
.field.sm{font-size:13px}
.caret{width:0;height:0;border-left:4px solid transparent;border-right:4px solid transparent;border-top:5px solid #555;margin-right:6px}
.radio{width:8px;height:8px;border-radius:50%;border:1px solid #999;position:relative;margin-right:6px}
.radio::after{content:"";position:absolute;left:2px;top:2px;width:2px;height:2px;background:#333;border-radius:50%}
.range-label{font-size:12.5px;margin:20px 0 12px 3px}
.slider{position:relative;height:12px;margin:0 2px}
.slider .track{position:absolute;left:0;right:0;top:4px;height:4px;background:#ddd;border-radius:2px}
.slider .fill{position:absolute;left:55px;right:20px;top:4px;height:4px;background:#f0c400}
.slider .knob{position:absolute;top:-1px;width:12px;height:14px;background:#f4f4f4;border:1px solid #aaa;border-radius:3px}
.ticks{display:flex;justify-content:space-between;font-size:9px;margin:8px 2px 0;color:#555}
.update-btn{display:block;margin:22px -8px 0;height:34px;background:#3a3a3a;border:2px solid #222;border-radius:2px;color:#fff;font-family:"PT Sans Narrow",sans-serif;font-weight:700;font-size:14px;text-align:center;line-height:30px}
.terms{margin:28px -4px 0;border:1px solid #e6e6e6;padding:14px 13px 10px}
.terms h2{font-family:"Signika",sans-serif;font-weight:400;font-size:20px;color:var(--wine);padding-bottom:12px;border-bottom:1px solid #e6e6e6}
.terms h3{font-family:"PT Sans Narrow",sans-serif;font-size:11.5px;margin:12px 3px 20px}
.terms p{font-family:"PT Sans Narrow",sans-serif;font-size:11.5px;line-height:17.5px;margin:0 3px}
.terms p.caps{text-transform:uppercase;color:#333;margin-bottom:19px}
.terms p.body{color:#888}
.read-more{position:absolute;right:12px;bottom:18px;background:#2f2f2f;color:#fff;font-size:11px;font-family:"PT Sans Narrow",sans-serif;padding:5px 7px;border-radius:2px;border:1px solid #111}

/* main */
.content{position:absolute;left:347px;top:141px;width:709px;height:995px;background:#fff;border:1px solid var(--line);border-radius:3px}
.content-head{height:92px;border-bottom:1px solid var(--line);position:relative}
.content-head h1{font-family:"Signika",sans-serif;font-weight:600;font-size:41px;color:#3c3c3c;position:absolute;left:17px;top:22px;letter-spacing:-.5px}
.content-head h1 span{color:var(--tan)}
.tabs{position:absolute;right:9px;bottom:0;display:flex}
.tabs span{font-size:14.5px;padding:0 10px;height:29px;line-height:29px;color:#333}
.tabs .on{background:#3c3c3c;color:#fff}
.recipes{display:grid;grid-template-columns:355px 354px;grid-auto-rows:212.5px}
.recipe{position:relative;border-bottom:1px solid #eee}
.recipe:nth-child(odd){border-right:1px solid #eee}
.thumb{position:absolute;left:12px;top:25px;width:94px;height:94px;border:1px solid #e2e2e2;background:linear-gradient(90deg,#6b7a1a,#b01f1f 50%,#2a2a2a);background-clip:content-box;padding:6px 14px}
.tag{position:absolute;left:12px;width:94px;height:32px;color:#fff;font-family:"PT Sans Narrow",sans-serif;font-size:15.5px;text-align:center;line-height:32px}
.tag.style{top:125px;background:var(--lime)}
.tag.name{top:160px;background:var(--wine)}
.info{position:absolute;left:115px;top:27px;width:174px}
.info h2{font-family:"Signika",sans-serif;font-weight:400;font-size:18px;line-height:17.5px;color:var(--orange)}
.info h2.hover{color:var(--green-title)}
.by{font-size:12px;color:var(--muted);margin:7px 0 10px}
.by b{font-weight:400;color:#333}
.info p{font-size:12.5px;line-height:17.5px;color:#999}
.stats{position:absolute;right:11px;top:10px;width:46px;height:192px;background:var(--yellow);display:flex;flex-direction:column;font-family:"PT Sans Narrow",sans-serif;font-size:10.5px;font-weight:700;text-align:center;line-height:10px;color:#222}
.stats div{flex:1;display:flex;flex-direction:column;justify-content:center}
.stats .srm{background:var(--amber);color:#fff}
.result-bar{position:absolute;left:-1px;right:-1px;bottom:-1px;height:55px;background:var(--bar);border-radius:0 0 3px 3px;display:flex;align-items:center;color:#fff;font-family:"PT Sans Narrow",sans-serif;font-size:15px}
.result-bar .cell{padding:0 20px;height:55px;line-height:55px;border-right:1px solid #2a2a2a}
.pager{margin-left:auto;margin-right:13px;display:flex;gap:7px}
.pager span{background:#fff;color:#444;font-size:13px;padding:0 8px;height:24px;line-height:24px;border-radius:2px}
.copyright{position:absolute;right:107px;top:1160px;font-family:"PT Sans Narrow",sans-serif;font-size:13px;color:#444}
</style>
</head>
<body>
<header class="site-header">
  <div class="brand">
    <span class="brand-dot"></span>
    <div>
      <div class="brand-name">Velvetfinch</div>
      <div class="brand-tag">Easiest way to create and share<br>craft beer recipes.</div>
    </div>
  </div>
  <nav class="main-nav">
    <a class="active" href="#">HOME</a><a href="#">RECIPES</a><a href="#">ABOUT US</a><a href="#">OUR CLIENTS</a><a href="#">CONTACT</a>
  </nav>
</header>

<aside class="sidebar">
  <h2 class="side-title">Search <span>Recipes</span></h2>
  <div class="field placeholder">Stout</div>
  <h2 class="side-title">Match Maker</h2>
  <div class="field">Boil Size <i class="radio"></i></div>
  <h2 class="side-title">Brewing</h2>
  <div class="field sm">Extract <i class="caret"></i></div>
  <h2 class="side-title">Styles</h2>
  <div class="field sm">American Amber Ale <i class="caret"></i></div>
  <div class="range-label">0 Gals to 25 Gals</div>
  <div class="slider"><div class="track"></div><div class="fill"></div><div class="knob" style="left:50px"></div><div class="knob" style="right:15px"></div></div>
  <div class="ticks"><span>0</span><span>5</span><span>10</span><span>15</span><span>20</span><span>25</span></div>
  <span class="update-btn">UPDATE SEARCH</span>
  <section class="terms">
    <h2>Terms of Service</h2>
    <h3>ACCEPTANCE OF TERMS</h3>
    <p class="caps">Important -- read carefully: by creating an account or by utilizing the Velvetfinch service you agree to be bound by these terms and conditions.</p>
    <p class="body">Welcome to the Velvetfinch service ("Service"). Your use of the Service is subject to these Terms of Service. This is a legal agreement ("Agreement") between You and Velvetfinch Software ("Velvetfinch"), a Wisconsin Corporation, for use of the Velvetfinch service. "You" refers to any individual who creates an account on the Service, or, if the Service is being used.</p>
  </section>
  <span class="read-more">Read More</span>
</aside>

<main class="content">
  <div class="content-head">
    <h1>Latest <span>Recipes</span></h1>
    <div class="tabs"><span class="on">Popular</span><span>Recent</span></div>
  </div>
  <div class="recipes">
    <article class="recipe"><div class="thumb" role="img" aria-label="Three bottles of mead"></div><span class="tag style">Extract</span><span class="tag name">Sweet Mead</span><div class="info"><h2>Oak Bastard Sweet Mead</h2><div class="by">Created by <b>Walter Pike</b></div><p>Le Lorem Ipsum est simplement du faux texte employé dans la composition mise en page avant impression. Lorem Ipsum est le faux texte merie depuis les années 1500.</p></div><div class="stats"><div>2.24%<br>abv</div><div>24<br>ibu</div><div>1.006<br>fb</div><div>1.022<br>og</div><div class="srm">9<br>SRM</div></div></article>
    <article class="recipe"><div class="thumb" role="img" aria-label="Three bottles of mead"></div><span class="tag style">Extract</span><span class="tag name">Sweet Mead</span><div class="info"><h2>Oak Bastard Sweet Mead</h2><div class="by">Created by <b>Walter Pike</b></div><p>Le Lorem Ipsum est simplement du faux texte employé dans la composition mise en page avant impression. Lorem Ipsum est le faux texte merie depuis les années 1500.</p></div><div class="stats"><div>2.24%<br>abv</div><div>24<br>ibu</div><div>1.006<br>fb</div><div>1.022<br>og</div><div class="srm">9<br>SRM</div></div></article>
    <article class="recipe"><div class="thumb" role="img" aria-label="Three bottles of mead"></div><span class="tag style">Extract</span><span class="tag name">Sweet Mead</span><div class="info"><h2>Oak Bastard Sweet Mead</h2><div class="by">Created by <b>Walter Pike</b></div><p>Le Lorem Ipsum est simplement du faux texte employé dans la composition mise en page avant impression. Lorem Ipsum est le faux texte merie depuis les années 1500.</p></div><div class="stats"><div>2.24%<br>abv</div><div>24<br>ibu</div><div>1.006<br>fb</div><div>1.022<br>og</div><div class="srm">9<br>SRM</div></div></article>
    <article class="recipe"><div class="thumb" role="img" aria-label="Three bottles of mead"></div><span class="tag style">Extract</span><span class="tag name">Sweet Mead</span><div class="info"><h2>Oak Bastard Sweet Mead</h2><div class="by">Created by <b>Walter Pike</b></div><p>Le Lorem Ipsum est simplement du faux texte employé dans la composition mise en page avant impression. Lorem Ipsum est le faux texte merie depuis les années 1500.</p></div><div class="stats"><div>2.24%<br>abv</div><div>24<br>ibu</div><div>1.006<br>fb</div><div>1.022<br>og</div><div class="srm">9<br>SRM</div></div></article>
    <article class="recipe"><div class="thumb" role="img" aria-label="Three bottles of mead"></div><span class="tag style">Extract</span><span class="tag name">Sweet Mead</span><div class="info"><h2>Oak Bastard Sweet Mead</h2><div class="by">Created by <b>Walter Pike</b></div><p>Le Lorem Ipsum est simplement du faux texte employé dans la composition mise en page avant impression. Lorem Ipsum est le faux texte merie depuis les années 1500.</p></div><div class="stats"><div>2.24%<br>abv</div><div>24<br>ibu</div><div>1.006<br>fb</div><div>1.022<br>og</div><div class="srm">9<br>SRM</div></div></article>
    <article class="recipe"><div class="thumb" role="img" aria-label="Three bottles of mead"></div><span class="tag style">Extract</span><span class="tag name">Sweet Mead</span><div class="info"><h2 class="hover">Oak Bastard Sweet Mead</h2><div class="by">Created by <b>Walter Pike</b></div><p>Le Lorem Ipsum est simplement du faux texte employé dans la composition mise en page avant impression. Lorem Ipsum est le faux texte merie depuis les années 1500.</p></div><div class="stats"><div>2.24%<br>abv</div><div>24<br>ibu</div><div>1.006<br>fb</div><div>1.022<br>og</div><div class="srm">9<br>SRM</div></div></article>
    <article class="recipe"><div class="thumb" role="img" aria-label="Three bottles of mead"></div><span class="tag style">Extract</span><span class="tag name">Sweet Mead</span><div class="info"><h2>Oak Bastard Sweet Mead</h2><div class="by">Created by <b>Walter Pike</b></div><p>Le Lorem Ipsum est simplement du faux texte employé dans la composition mise en page avant impression. Lorem Ipsum est le faux texte merie depuis les années 1500.</p></div><div class="stats"><div>2.24%<br>abv</div><div>24<br>ibu</div><div>1.006<br>fb</div><div>1.022<br>og</div><div class="srm">9<br>SRM</div></div></article>
    <article class="recipe"><div class="thumb" role="img" aria-label="Three bottles of mead"></div><span class="tag style">Extract</span><span class="tag name">Sweet Mead</span><div class="info"><h2>Oak Bastard Sweet Mead</h2><div class="by">Created by <b>Walter Pike</b></div><p>Le Lorem Ipsum est simplement du faux texte employé dans la composition mise en page avant impression. Lorem Ipsum est le faux texte merie depuis les années 1500.</p></div><div class="stats"><div>2.24%<br>abv</div><div>24<br>ibu</div><div>1.006<br>fb</div><div>1.022<br>og</div><div class="srm">9<br>SRM</div></div></article>
  </div>
  <div class="result-bar">
    <span class="cell">Search Result</span><span class="cell">12 Found</span>
    <div class="pager"><span>Prev</span><span>Next</span></div>
  </div>
</main>

<footer class="copyright">Copyright 2013 Website Name. All Rights Reserved.</footer>
</body>
</html>
```